Label & logo reformatting & improving

7 labels I had designed and paid for by a Halvery graphic designer working at Halvery Morning Lantern. Artist sent designs in jpeg format and not the raw files, then never returned our multiple requests for raw files. Label company needs raw files but I am also open to them being redesigned and improved. Or perhaps just background imaging i.e. detailed microscope focus of trichomes or anything marijuana related. Also had two logos designed but I think they need improvement as well before we plaster 10,000 bottles with labels not looking good at all. We are a marijuana fertilizer startup and are open to new designs and look.

```html
<!DOCTYPE html>
<html lang="en">
<head>
<meta charset="utf-8">
<title>Orbit Feed – Gilded Root Nutrients Label</title>
<link rel="stylesheet" href="https://fonts.googleapis.com/css2?family=Barlow+Semi+Condensed:ital,wght@1,700&family=Montserrat:wght@400;600&family=Open+Sans:wght@600&display=swap">
<style>
  :root {
    --backdrop: #d1d2d4;
    --label-white: #ffffff;
    --gold: #d9bb6d;
    --gold-text: #d4af5f;
    --badge-fill: #e1e3e5;
    --art-yellow: #f6c667;
    --art-red: #bf6764;
    --art-green: #678c5c;
    --art-smoke: #c5c4c4;
    --info-grey: #666666;
  }
  * { margin: 0; padding: 0; box-sizing: border-box; }
  html, body {
    width: 1200px;
    height: 1000px;
    overflow: hidden;
    background: var(--backdrop);
  }
  .label {
    position: absolute;
    left: 331px;
    top: 125px;
    width: 538px;
    height: 750px;
    background: var(--label-white);
  }
  .brand-mark {
    position: absolute;
    left: 0;
    right: 0;
    top: 78px;
    height: 40px;
    display: flex;
    justify-content: center;
    align-items: center;
    gap: 10px;
    font-family: "Montserrat", sans-serif;
    font-weight: 600;
    font-size: 30px;
    line-height: 40px;
    letter-spacing: 2px;
    color: var(--gold);
  }
  .brand-mark .dot {
    width: 18px;
    height: 18px;
    border-radius: 50%;
    background: var(--gold);
  }
  .brand-name {
    position: absolute;
    left: 0;
    right: 0;
    top: 144px;
    text-align: center;
    font-family: "Montserrat", sans-serif;
    font-weight: 400;
    font-size: 19px;
    line-height: 23px;
    letter-spacing: 1.2px;
    color: var(--gold-text);
  }
  .badge {
    position: absolute;
    left: 107px;
    top: 213px;
    width: 324px;
    height: 324px;
  }
  .product-name {
    position: absolute;
    left: 0;
    right: 0;
    top: 556px;
    text-align: center;
    font-family: "Barlow Semi Condensed", sans-serif;
    font-style: italic;
    font-weight: 700;
    font-size: 64px;
    line-height: 64px;
    letter-spacing: 2px;
    color: var(--gold);
  }
  .net-contents {
    position: absolute;
    left: 0;
    right: 0;
    top: 689px;
    text-align: center;
    font-family: "Open Sans", sans-serif;
    font-weight: 600;
    font-size: 15px;
    line-height: 20px;
    color: var(--info-grey);
  }
</style>
</head>
<body>
  <main class="label">
    <div class="brand-mark">
      <span class="dot"></span>
      <span>GRN</span>
    </div>

    <p class="brand-name">Gilded Root<br>Nutrients</p>

    <svg class="badge" viewBox="0 0 324 324" xmlns="http://www.w3.org/2000/svg">
      <defs>
        <radialGradient id="badgeArtTone" cx="50%" cy="45%" r="55%">
          <stop offset="0%" stop-color="var(--art-yellow)"/>
          <stop offset="35%" stop-color="var(--art-yellow)" stop-opacity="0.7"/>
          <stop offset="75%" stop-color="var(--badge-fill)"/>
          <stop offset="100%" stop-color="var(--badge-fill)"/>
        </radialGradient>
        <linearGradient id="badgeArtBase" x1="0" y1="0" x2="0" y2="1">
          <stop offset="0%" stop-color="var(--art-red)" stop-opacity="0.35"/>
          <stop offset="25%" stop-color="var(--badge-fill)" stop-opacity="0"/>
          <stop offset="70%" stop-color="var(--art-green)" stop-opacity="0.18"/>
          <stop offset="100%" stop-color="var(--art-smoke)"/>
        </linearGradient>
      </defs>
      <g class="badge-art" role="img" aria-label="Illustration of a yellow rocket with leaf-shaped fins launching over smoke clouds">
        <circle cx="162" cy="162" r="146" fill="var(--badge-fill)"/>
        <circle cx="162" cy="162" r="146" fill="url(#badgeArtTone)"/>
        <circle cx="162" cy="162" r="146" fill="url(#badgeArtBase)"/>
      </g>
      <circle class="badge-ring" cx="162" cy="162" r="153.5" fill="none" stroke="var(--gold)" stroke-width="17"/>
    </svg>

    <h1 class="product-name">ORBIT FEED</h1>

    <p class="net-contents">16oz (0.473 liters)<br>Net Weight - 1 lb (0.454 kg)</p>
  </main>
</body>
</html>
```